QVR business card

Need a business card for a company that provides instructional design and elearning development services. The website is here: http://quorvane.studio/

I'm attaching a current logo, as well as the old business card design. While I like to keep it clean, the old design is too simplistic for my liking. The only idea I want to reuse from the old design is placing industry jargon on the back of the card, just need a better way to present it. But if you have other ideas for the back--feel free to experiment.

Please use the colors complementary to the color we have on the website. Thank you!

```html
<!DOCTYPE html>
<html lang="en">
<head>
<meta charset="utf-8">
<title>QVR business card</title>
<link rel="stylesheet" href="https://fonts.googleapis.com/css2?family=Raleway:wght@600;700&family=Roboto:wght@400;700;900&display=swap">
<style>
  :root {
    --backdrop: #e4e4e4;
    --card-white: #ffffff;
    --gold: #dccf93;
    --teal: #1aa9a4;
    --jargon-grey: #6b6b6b;
    --ink-white: #ffffff;
  }
  * { box-sizing: border-box; margin: 0; padding: 0; }
  html, body { width: 1200px; height: 800px; overflow: hidden; }
  body {
    background: var(--backdrop);
    font-family: "Roboto", Arial, sans-serif;
    position: relative;
  }
  .card {
    position: absolute;
    top: 240px;
    width: 540px;
    height: 320px;
    border-radius: 22px;
    overflow: hidden;
    background: var(--card-white);
    box-shadow: 0 8px 22px rgba(0,0,0,0.18);
  }
  /* Back side: industry jargon */
  .card--back { left: 40px; padding: 44px 36px 0 36px; }
  .jargon {
    color: var(--jargon-grey);
    font-weight: 700;
    font-size: 21px;
    line-height: 26px;
    letter-spacing: 0.2px;
    white-space: nowrap;
  }
  .headline {
    color: var(--teal);
    font-weight: 400;
    font-size: 46px;
    line-height: 52px;
    margin: 12px 0 14px;
    white-space: nowrap;
  }
  /* Front side: identity and contact */
  .card--front { left: 620px; }
  .front-shape { position: absolute; inset: 0; }
  .brand {
    position: absolute;
    left: 0;
    top: 0;
    width: 140px;
    height: 320px;
    display: flex;
    flex-direction: column;
    align-items: center;
    justify-content: center;
    gap: 12px;
  }
  .brand-dot {
    width: 22px; height: 22px;
    border-radius: 50%;
    background: var(--teal);
  }
  .brand-name {
    font-family: "Raleway", sans-serif;
    font-weight: 700;
    font-size: 40px;
    color: var(--teal);
    letter-spacing: 1px;
  }
  .holder {
    position: absolute;
    left: 185px;
    top: 46px;
    font-family: "Raleway", sans-serif;
    font-weight: 700;
    font-size: 34px;
    color: var(--ink-white);
    white-space: nowrap;
  }
  .contacts {
    position: absolute;
    left: 180px;
    top: 150px;
    list-style: none;
  }
  .contact {
    display: flex;
    align-items: center;
    gap: 12px;
    color: var(--ink-white);
    font-size: 19px;
    line-height: 36px;
    white-space: nowrap;
  }
  .contact svg { width: 20px; height: 20px; flex: none; }
</style>
</head>
<body>

  <section class="card card--back" aria-label="Card back">
    <p class="jargon">MOBILE LEARNING SCORM INSTRUCTIONAL</p>
    <p class="jargon">DESIGN LMS MOOCS ELEARNING HTML5</p>
    <h2 class="headline">HOW CAN WE HELP?</h2>
    <p class="jargon">ADULT LEARNING THEORY GAMIFICATION</p>
    <p class="jargon">CLASSROOM XAPI BLENDED LEARNING</p>
  </section>

  <section class="card card--front" aria-label="Card front">
    <svg class="front-shape" viewBox="0 0 540 320" width="540" height="320" aria-hidden="true">
      <path fill="var(--gold)" d="M150 0 H540 V320 H150 V218 L128 204 L150 192 V140 L126 124 L150 112 V60 L130 46 L150 36 Z"/>
    </svg>

    <div class="brand">
      <span class="brand-dot"></span>
      <span class="brand-name">QVR</span>
    </div>

    <h1 class="holder">Marcus Tellavane</h1>

    <ul class="contacts">
      <li class="contact">
        <svg viewBox="0 0 24 24" aria-hidden="true"><path fill="#fff" d="M6.6 10.8a15 15 0 0 0 6.6 6.6l2.2-2.2a1 1 0 0 1 1-.25 11.4 11.4 0 0 0 3.6.57 1 1 0 0 1 1 1V20a1 1 0 0 1-1 1A17 17 0 0 1 3 4a1 1 0 0 1 1-1h3.5a1 1 0 0 1 1 1c0 1.25.2 2.45.57 3.57a1 1 0 0 1-.25 1z"/></svg>
        <span>212-555-0187</span>
      </li>
      <li class="contact">
        <svg viewBox="0 0 24 24" aria-hidden="true"><rect x="2" y="5" width="20" height="14" rx="1" fill="none" stroke="#fff" stroke-width="2"/><path d="M2 6 L12 13 L22 6" fill="none" stroke="#fff" stroke-width="2"/></svg>
        <span>mtellavane@quorvane.studio</span>
      </li>
      <li class="contact">
        <svg viewBox="0 0 24 24" aria-hidden="true"><rect x="2" y="3" width="20" height="14" rx="1" fill="none" stroke="#fff" stroke-width="2"/><path d="M8 21 H16 M12 17 V21" stroke="#fff" stroke-width="2"/></svg>
        <span>www.quorvane.studio</span>
      </li>
    </ul>
  </section>

</body>
</html>
```